Fresh, modern, fun business card for pediatric dental practice

Need a business card for fresh, modern, fun pediatric dental practice

Clean look that matches our website's font and colors

We prefer the look of curved corners on business cards

Target Market(s)

parents (mothers) of young children, professionals, mid-high class

Industry/Entity Type

Dental

Contact Information for Business Card

Maplebrook Pediatric Dentistry
482 Quarry Lane
Suite 517
Alderton, PA 17599
717.555.0193
www.maplebrookkidsdental.example

Mei-Ran Tsai, DMD
Corinne Walbeck, DMD
(we are working on our email address, but we would like that on the card as well)

Font styles to use
Sans Serif

Requirements
Must have
• All info; we would also like to make cards for individual staff members
• colors from our website and color palatte, attatched
• use same font and design as website for branding
Nice to have
• clean, simple card that has a pop of color
• we would like to see a few designs with our tag line "where smiles get brighter"
• we are not sure if we want to have it on there or not
• we would like to see a few designs incorporating the ribbon graphic on our website where the word WELCOME is

```html
<!DOCTYPE html>
<html lang="en">
<head>
<meta charset="utf-8">
<title>Maplebrook Pediatric Dentistry – Business Cards</title>
<link href="https://fonts.googleapis.com/css2?family=Lato:wght@400;700;900&display=swap" rel="stylesheet">
<style>
  :root {
    --backdrop: #3b3731;
    --card-plum: #4a1d47;
    --sun-yellow: #f5b324;
    --berry-pink: #d83f9e;
    --text-white: #f4eef3;
    --card-radius: 18px;
  }
  * { box-sizing: border-box; margin: 0; padding: 0; }
  html, body {
    width: 1200px; height: 930px; overflow: hidden;
    background: var(--backdrop);
    font-family: "Lato", sans-serif;
  }
  .stage { position: relative; width: 1200px; height: 930px; }
  .card {
    position: absolute;
    width: 560px; height: 320px;
    background: var(--card-plum);
    border-radius: var(--card-radius);
    box-shadow: 0 14px 30px rgba(0,0,0,0.45);
    color: var(--text-white);
  }
  .card--front { left: 70px; top: 90px; }
  .card--back { left: 570px; top: 500px; }

  /* Wordmark */
  .wordmark {
    display: flex; align-items: center; gap: 12px;
    color: var(--sun-yellow);
    font-weight: 900;
    line-height: 1.05;
  }
  .wordmark__dot {
    flex: none;
    width: 34px; height: 34px; border-radius: 50%;
    background: var(--sun-yellow);
  }
  .wordmark__name { font-size: 30px; letter-spacing: 0.5px; }

  .card--front .wordmark {
    position: absolute; left: 0; right: 0; top: 110px;
    justify-content: center;
  }
  .front__web {
    position: absolute; left: 0; right: 0; top: 236px;
    text-align: center;
    font-size: 15px; letter-spacing: 1px;
    color: var(--text-white);
  }

  /* Back */
  .card--back .wordmark {
    position: absolute; left: 34px; top: 170px; width: 220px;
    align-items: flex-start;
  }
  .card--back .wordmark__dot { width: 26px; height: 26px; margin-top: 4px; }
  .card--back .wordmark__name { font-size: 22px; }
  .back__divider {
    position: absolute; left: 270px; top: 70px;
    width: 2px; height: 180px;
    background: var(--berry-pink);
  }
  .contact {
    position: absolute; left: 292px; top: 66px; right: 20px;
  }
  .contact__name {
    color: var(--sun-yellow); font-weight: 700;
    font-size: 19px; letter-spacing: 0.6px; text-transform: uppercase;
  }
  .contact__title { font-size: 13px; margin-top: 2px; }
  .contact__practice {
    color: var(--sun-yellow); font-size: 12px; margin-top: 10px;
  }
  .contact__address { font-size: 12px; line-height: 1.4; font-style: normal; }
  .contact__list { list-style: none; margin-top: 12px; }
  .contact__item {
    display: flex; align-items: center; gap: 8px;
    font-size: 12px; line-height: 1.7;
  }
  .contact__icon { width: 12px; height: 12px; flex: none; fill: var(--sun-yellow); }
</style>
</head>
<body>
<main class="stage">

  <section class="card card--front" aria-label="Card front">
    <div class="wordmark">
      <span class="wordmark__dot"></span>
      <span class="wordmark__name">Maplebrook<br>Pediatric Dentistry</span>
    </div>
    <p class="front__web">www.maplebrookkidsdental.example</p>
  </section>

  <section class="card card--back" aria-label="Card back">
    <div class="wordmark">
      <span class="wordmark__dot"></span>
      <span class="wordmark__name">Maplebrook Pediatric Dentistry</span>
    </div>
    <div class="back__divider"></div>
    <div class="contact">
      <h1 class="contact__name">Corinne Walbeck</h1>
      <p class="contact__title">DMD</p>
      <p class="contact__practice">Maplebrook Pediatric Dentistry</p>
      <address class="contact__address">482 Quarry Lane<br>Suite 517 Alderton, PA 17599</address>
      <ul class="contact__list">
        <li class="contact__item">
          <svg class="contact__icon" viewBox="0 0 24 24" aria-hidden="true"><path d="M6.6 10.8a15.1 15.1 0 0 0 6.6 6.6l2.2-2.2a1 1 0 0 1 1-.25 11.4 11.4 0 0 0 3.6.57 1 1 0 0 1 1 1V20a1 1 0 0 1-1 1A17 17 0 0 1 3 4a1 1 0 0 1 1-1h3.5a1 1 0 0 1 1 1c0 1.25.2 2.450.57 3.57a1 1 0 0 1-.25 1z"/></svg>
          717.555.0193
        </li>
        <li class="contact__item">
          <svg class="contact__icon" viewBox="0 0 24 24" aria-hidden="true"><path d="M2 5h20v14H2z M2 5l10 8 10-8" fill="none" stroke="#f5b324" stroke-width="2.4"/></svg>
          info@maplebrookkidsdental.example
        </li>
        <li class="contact__item">
          <svg class="contact__icon" viewBox="0 0 24 24" aria-hidden="true"><circle cx="12" cy="12" r="9.5" fill="none" stroke="#f5b324" stroke-width="2"/><path d="M2.5 12h19M12 2.5c3 3 3 16 0 19M12 2.5c-3 3-3 16 0 19" fill="none" stroke="#f5b324" stroke-width="1.8"/></svg>
          www.maplebrookkidsdental.example
        </li>
      </ul>
    </div>
  </section>

</main>
</body>
</html>
```